Stationery Design Project for Nimbora, Chicago

Nimbora, a street parking application which helps car drivers find a street parking spot by offering an ideal path along which to look for parking. This path is calculated by our algorithm based on data (e.g. historical data, baseball games schedule, etc.). Along this path the driver will find a spot and will also save 70% of the search time. Customer we target is reg. between 21 and 45 yo.

We envision something young, fresh, bright and original. Slightly abstract maybe. It should represent the idea and elements of finding street parking in the city, e.g. car(s), parking spot, people, city, etc. (just ideas!).

Logo is attached.

Requirement:
- Business Cards (2 Sided Full Color CMYK)
- Letterhead (1 Sided Full Color CMYK)
- Envelope (1 Sided Full Color CMYK)
- Sticker (1 Sided Full Color CMYK), round with a 2inch diameter.

Reason: We're starting to get more and more designs and need more time to look into all of them. Very exciting!! Thanks to everybody!

Hi all, we're in the process of selecting our favs. Though choices!!! Really good submissions. Will keep you posted and sorry for the delay.

Target Market(s)

Car drivers and owners between 21 and 45

Industry/Entity Type

Parking

Requirements
Must have
• Sticker should be round and include company URL nimbora.com and the new logo which we will attach soon.
Should not have
• Should not be too serious or boring.

```html
<!DOCTYPE html>
<html lang="en">
<head>
<meta charset="utf-8">
<title>Nimbora Business Card</title>
<link href="https://fonts.googleapis.com/css2?family=Open+Sans:wght@400;600;700&display=swap" rel="stylesheet">
<style>
  :root {
    --backdrop: #e9e6e1;
    --card-white: #ffffff;
    --brand-blue: #1f5cb4;
    --brand-blue-deep: #163f8f;
    --brand-blue-light: #3c82d6;
    --name-blue: #2a9ad6;
    --ink-dark: #2b2b2e;
    --band-black: #1c1c1e;
    --text-white: #ffffff;
  }
  html, body {
    margin: 0;
    padding: 0;
    width: 1200px;
    height: 395px;
    overflow: hidden;
    background: var(--backdrop);
    font-family: "Open Sans", Arial, sans-serif;
  }
  .canvas {
    position: relative;
    width: 1200px;
    height: 395px;
  }
  .card {
    position: absolute;
    top: 47px;
    width: 517px;
    height: 296px;
    box-shadow: 0 2px 6px rgba(0,0,0,0.25);
    overflow: hidden;
  }
  .card-front { left: 61px; background: var(--card-white); }
  .card-back {
    left: 628px;
    background: radial-gradient(ellipse at 50% 45%, var(--brand-blue-light) 0%, var(--brand-blue) 55%, var(--brand-blue-deep) 100%);
  }
  .front-waves { position: absolute; inset: 0; }
  .brand {
    position: absolute;
    left: 40px;
    top: 30px;
    display: flex;
    align-items: center;
    gap: 18px;
  }
  .brand-dot {
    width: 84px;
    height: 84px;
    border-radius: 50%;
    background: var(--brand-blue);
  }
  .brand-name {
    font-size: 52px;
    font-weight: 600;
    color: var(--ink-dark);
    letter-spacing: 0.5px;
  }
  .person {
    position: absolute;
    left: 44px;
    top: 174px;
    font-size: 21px;
    font-weight: 700;
    color: var(--name-blue);
  }
  .person .title { font-weight: 400; font-size: 17px; }
  .contacts {
    position: absolute;
    right: 22px;
    top: 187px;
    list-style: none;
    margin: 0;
    padding: 0;
    text-align: right;
    color: var(--text-white);
    font-size: 12.5px;
    line-height: 19px;
  }
  .contacts li { display: flex; justify-content: flex-end; align-items: center; gap: 5px; }
  .contacts svg { width: 10px; height: 10px; fill: var(--text-white); }
  .address {
    position: absolute;
    right: 22px;
    bottom: 12px;
    color: var(--text-white);
    font-size: 12.5px;
  }
  .back-brand {
    position: absolute;
    inset: 0;
    display: flex;
    flex-direction: column;
    align-items: center;
  }
  .back-dot {
    margin-top: 60px;
    width: 136px;
    height: 136px;
    border-radius: 50%;
    background: var(--brand-blue-light);
  }
  .back-name {
    margin-top: 14px;
    font-size: 26px;
    font-weight: 600;
    color: var(--text-white);
  }
  .back-url {
    position: absolute;
    left: 0; right: 0;
    bottom: 24px;
    text-align: center;
    color: var(--text-white);
    font-size: 17px;
    letter-spacing: 2px;
  }
</style>
</head>
<body>
<main class="canvas">
  <section class="card card-front">
    <svg class="front-waves" viewBox="0 0 517 296" preserveAspectRatio="none" aria-hidden="true">
      <defs>
        <linearGradient id="blueWave" x1="0" y1="0" x2="1" y2="1">
          <stop offset="0" stop-color="#2a6ccc"/>
          <stop offset="1" stop-color="#16449b"/>
        </linearGradient>
      </defs>
      <path d="M0,248 C120,272 255,232 338,188 C410,152 468,140 517,142 L517,296 L0,296 Z" fill="url(#blueWave)"/>
      <path d="M0,230 C130,270 258,212 338,170 C420,130 478,126 517,130 L517,140 C468,137 410,150 338,186 C258,226 130,266 0,248 Z" fill="var(--band-black)"/>
      <path d="M0,256 C140,276 270,238 350,196 C420,162 470,152 517,152" fill="none" stroke="#ffffff" stroke-width="2" opacity="0.8"/>
      <path d="M60,262 C170,268 280,236 360,200 C430,170 480,160 517,160" fill="none" stroke="#7fb6ec" stroke-width="1.5" opacity="0.7"/>
    </svg>
    <div class="brand">
      <div class="brand-dot"></div>
      <div class="brand-name">Nimbora</div>
    </div>
    <div class="person">Your Name , <span class="title">Title</span></div>
    <ul class="contacts">
      <li>+91 12345 67890 <svg viewBox="0 0 10 10"><circle cx="5" cy="5" r="5"/></svg></li>
      <li>+91 12345 67890 <svg viewBox="0 0 10 10"><rect x="2.5" y="0" width="5" height="10" rx="1"/></svg></li>
      <li>info@nimbora.com <svg viewBox="0 0 10 10"><rect x="0" y="2" width="10" height="6"/></svg></li>
      <li>www.nimbora.com <svg viewBox="0 0 10 10"><circle cx="5" cy="5" r="5"/></svg></li>
    </ul>
    <div class="address">Complex Name, Street Name, Area, City Name,000 000</div>
  </section>

  <section class="card card-back">
    <div class="back-brand">
      <div class="back-dot"></div>
      <div class="back-name">Nimbora</div>
    </div>
    <div class="back-url">www.nimbora.com</div>
  </section>
</main>
</body>
</html>
```